Job application set/company logo

My resume, profile and project file need to be designed in a common, fresh business design, not too playful and colourful
Potentially a logo for my company called Silver Reed Consulting needs to be designed in a second step. My company is consulting in digitalization and business transformation.

```html
<!DOCTYPE html>
<html lang="en">
<head>
<meta charset="utf-8">
<title>Marcus Hallberg – Resume</title>
<link href="https://fonts.googleapis.com/css2?family=Oswald:wght@500;700&family=Open+Sans:wght@400;600;700&display=swap" rel="stylesheet">
<style>
:root{
  --navy:#1f2a36;
  --navy-2:#2a3644;
  --mist:#c8d5db;
  --orange:#e8742a;
  --ink:#2b2b2b;
  --muted:#5d6670;
  --paper:#ffffff;
  --bg:#f4f5f6;
}
*{box-sizing:border-box;margin:0;padding:0}
html,body{width:696px;height:1200px;overflow:hidden;background:var(--bg);font-family:"Open Sans",Arial,sans-serif;color:var(--ink)}
.page{position:absolute;left:40px;width:616px;background:var(--paper);box-shadow:0 2px 8px rgba(0,0,0,.18);display:flex;overflow:hidden}
.page-one{top:24px;height:566px}
.page-two{top:614px;height:566px}
.sidebar{width:236px;display:flex;flex-direction:column;flex-shrink:0}
.main{flex:1;padding:18px 20px 10px 18px;font-size:6.6px;line-height:1.45}
.portrait{height:168px;background:linear-gradient(160deg,#8c8f93 0%,#4d5560 55%,#2d3540 100%)}
.dark{background:var(--navy);color:#fff;padding:12px 18px}
.light{background:var(--mist);color:var(--navy);padding:12px 18px;flex:1}
.name{font-family:"Oswald",sans-serif;font-weight:700;font-size:34px;line-height:1;text-transform:uppercase;letter-spacing:.5px}
.name .last{color:var(--orange);display:block}
.side-title{font-family:"Oswald",sans-serif;font-weight:500;font-size:14px;letter-spacing:2px;text-transform:uppercase;margin:12px 0 6px}
.side-title.accent{color:var(--orange)}
.contact{list-style:none;font-size:6.6px;line-height:1.9}
.contact li{display:flex;align-items:center;gap:6px}
.contact svg{width:8px;height:8px;flex-shrink:0}
.box{background:var(--paper);border-left:3px solid var(--orange);padding:6px 8px;margin-bottom:8px;font-size:6.4px;line-height:1.5}
.box h4{font-size:6.8px;color:var(--orange);text-transform:uppercase;margin-bottom:3px}
.box ul{padding-left:9px}
.section-title{font-family:"Oswald",sans-serif;font-weight:700;font-size:15px;text-transform:uppercase;color:var(--navy);line-height:1.05;margin-bottom:8px}
.section-title .accent{color:var(--orange)}
.achievement{display:flex;gap:7px;margin-bottom:8px}
.achievement svg{width:10px;height:10px;flex-shrink:0;margin-top:1px}
.achievement h5{font-size:6.8px;color:var(--orange);text-transform:uppercase;margin-bottom:2px}
.achievement ul,.role ul{padding-left:9px}
.role{margin-bottom:7px}
.role h5{font-size:6.8px;color:var(--navy)}
.role .when{color:var(--muted)}
.employer{font-family:"Oswald",sans-serif;font-weight:500;font-size:10px;text-transform:uppercase;color:var(--orange);margin:8px 0 5px;display:flex;align-items:center;gap:6px}
.employer::before{content:"";width:7px;height:7px;background:var(--orange);display:inline-block}
.side-text{font-size:6.8px;line-height:1.55}
.side-text p{margin-bottom:5px}
.side-list{list-style:none;font-size:6.8px;line-height:1.7}
.side-list li::before{content:"•";color:var(--orange);margin-right:5px}
.page-two .dark{flex:0 0 330px}
</style>
</head>
<body>

<section class="page page-one">
  <aside class="sidebar">
    <div class="portrait" role="img" aria-label="Portrait photo of Marcus Hallberg in a dark suit"></div>
    <div class="dark">
      <h1 class="name">Marcus<span class="last">Hallberg</span></h1>
      <h2 class="side-title">Personal Info</h2>
      <ul class="contact">
        <li><svg viewBox="0 0 10 10"><rect x="1" y="2" width="8" height="6" fill="none" stroke="#e8742a"/><path d="M1 2l4 3 4-3" fill="none" stroke="#e8742a"/></svg>marcus.hallberg@mail.com</li>
        <li><svg viewBox="0 0 10 10"><path d="M5 9C2 5 2 4 2 3.5a3 3 0 016 0C8 4 8 5 5 9z" fill="#e8742a"/></svg>Lindenweg 12, 50667 Cologne</li>
        <li><svg viewBox="0 0 10 10"><path d="M2 1h2l1 2-1 1c1 2 2 3 3 3l1-1 2 1v2c-5 0-8-3-8-8z" fill="#e8742a"/></svg>+49 170 555 0142</li>
        <li><svg viewBox="0 0 10 10"><circle cx="5" cy="5" r="3.5" fill="none" stroke="#e8742a"/></svg>linkedin.example/marcushallberg</li>
      </ul>
    </div>
    <div class="light">
      <h2 class="side-title">Qualifications</h2>
      <div class="box">
        <h4>Core Competencies</h4>
        <ul>
          <li>Digital transformation strategy and roadmaps</li>
          <li>Business model innovation and venture building</li>
          <li>Leadership of cross-functional teams</li>
        </ul>
      </div>
      <div class="box">
        <h4>Accomplishments</h4>
        <ul>
          <li>Led nationwide rollout of a new digital service</li>
          <li>Built partner network across three markets</li>
          <li>Won internal innovation award twice</li>
        </ul>
      </div>
    </div>
  </aside>
  <div class="main">
    <h2 class="section-title">Profile &amp;<br><span class="accent">Achievements</span></h2>
    <div class="achievement">
      <svg viewBox="0 0 10 10"><rect width="10" height="10" fill="#e8742a"/></svg>
      <div><h5>Seasoned entrepreneurial innovator</h5>
      <ul><li>Over 15 years shaping new digital businesses in telecom</li><li>Turns early ideas into scalable products with clear value</li><li>Drives change with pragmatic, data-led decisions</li></ul></div>
    </div>
    <div class="achievement">
      <svg viewBox="0 0 10 10"><rect width="10" height="10" fill="#e8742a"/></svg>
      <div><h5>Leading global partnership networks</h5>
      <ul><li>Negotiated strategic alliances with global technology firms</li><li>Built lasting trust with senior partners and investors</li><li>Aligned partner goals with company growth targets</li></ul></div>
    </div>
    <div class="achievement">
      <svg viewBox="0 0 10 10"><rect width="10" height="10" fill="#e8742a"/></svg>
      <div><h5>Delivery-oriented product leader</h5>
      <ul><li>Managed product portfolios with strong revenue results</li><li>Coached teams toward agile ways of working</li><li>Known for a calm, structured and reliable approach</li></ul></div>
    </div>
    <h2 class="section-title" style="margin-top:10px">Experience</h2>
    <div class="employer">Senior Advisor <span style="color:var(--navy)">(self-employed)</span></div>
    <div class="role"><h5>Innovation Consulting <span class="when">· since 2021</span></h5>
      <ul><li>Advises mid-sized firms on digital growth strategy</li><li>Designs new service models and operating structures</li></ul></div>
    <div class="role"><h5>Interim Program Lead <span class="when">· 2020 – 2021</span></h5>
      <ul><li>Steered transformation program for a regional utility</li><li>Established governance and delivery cadence</li></ul></div>
    <div class="role"><h5>Board Advisor <span class="when">· 2019 – 2020</span></h5>
      <ul><li>Supported two start-ups in funding and go-to-market</li></ul></div>
  </div>
</section>

<section class="page page-two">
  <aside class="sidebar">
    <div class="dark">
      <h2 class="side-title accent">University</h2>
      <div class="side-text">
        <p>Executive Leadership Development Program at Westbrook Graduate School of Business<br>2015</p>
        <p>Diploma in Electrical Engineering at Lindenau University of Applied Sciences<br>1998</p>
      </div>
      <h2 class="side-title accent">Languages</h2>
      <ul class="side-list"><li>German (native)</li><li>English (full professional proficiency)</li></ul>
      <h2 class="side-title accent">Activities</h2>
      <ul class="side-list"><li>Sport: Skiing, Tennis, Hiking, Yoga</li><li>Music: Classical Piano</li><li>Travelling: Europe, Africa, America</li></ul>
    </div>
    <div class="light">
      <h2 class="side-title">References</h2>
      <ul class="side-list">
        <li>Thomas Berger, CEO Northline Telecom</li>
        <li>Michael Kraus, SVP Mobile Strategy, Projects and Marketing Partnerships, Northline Telecom</li>
        <li>Yvonne Matthes, Senior Director, Korvel Corporation</li>
      </ul>
    </div>
  </aside>
  <div class="main">
    <div class="role"><h5>Silver Reed Consulting <span class="when">· 2018 – 2019</span></h5>
      <ul><li>Founded advisory practice for digital transformation</li><li>Delivered strategy projects for industrial clients</li></ul></div>
    <div class="employer">Northline Telecom AG, Bonn</div>
    <div class="role"><h5>Senior Vice President Business Development <span class="when">· 2012 – 2018</span></h5>
      <ul><li>Managed new digital growth areas with global partners</li><li>Launched first joint offers with major device makers</li><li>Led team of 40 across product, sales and marketing</li></ul></div>
    <div class="role"><h5>Vice President Product Management <span class="when">· 2008 – 2012</span></h5>
      <ul><li>Introduced new mobile service bundles nationwide</li><li>Raised customer satisfaction through simpler offers</li><li>Coordinated launches with marketing and retail teams</li></ul></div>
    <div class="role"><h5>Head of Product Management <span class="when">· 2005 – 2008</span></h5>
      <ul><li>Built product roadmap for mobile data services</li><li>Grew data revenue with clear pricing structures</li></ul></div>
    <div class="employer">Meridian Mobile International, Bonn</div>
    <div class="role"><h5>Head of Portfolio Strategy <span class="when">· 2002 – 2005</span></h5>
      <ul><li>Aligned product portfolio across European subsidiaries</li><li>Set up shared roadmap process with country teams</li><li>Prepared board decisions on new services</li></ul></div>
    <div class="role"><h5>Project Lead Mobile Services <span class="when">· 1999 – 2002</span></h5>
      <ul><li>Led early mobile internet launch projects</li><li>Worked closely with network and IT engineering</li></ul></div>
    <div class="role"><h5>Product Engineer <span class="when">· 1998 – 1999</span></h5>
      <ul><li>Tested new handsets and network features</li></ul></div>
  </div>
</section>

</body>
</html>
```